I am looking for a modern, clean and neat design for a reflexology and well being business. The business name is Gralo Tund (this is an old Latin word for wellbeing). The colours I would like are purple, white and grey. I am open to suggestions for pictures such as healing or working hands, a pair of feet, images that represent my business that you may think of....... or maybe you think no images at all would be best? My tag line is: "Relax, Renew, Revive" or "Find you balance......... Relax, Renew, Revive" I can decide which I want so I would like to see what both would look like. I would like space on the back to write the client's appointment date and time (more than once)

```html
<!DOCTYPE html>
<html lang="en">
<head>
<meta charset="utf-8">
<title>Gralo Tund – Business &amp; Appointment Card</title>
<link rel="stylesheet" href="https://fonts.googleapis.com/css2?family=Open+Sans:wght@400;600;700&display=swap">
<style>
  :root {
    --purple: #a000b8;
    --white: #ffffff;
    --grey: #3f3f42;
    --backdrop: #e9e7ea;
    --rule: rgba(255,255,255,0.28);
  }
  * { box-sizing: border-box; margin: 0; padding: 0; }
  html, body {
    width: 1200px; height: 900px; overflow: hidden;
    background: var(--backdrop);
    font-family: "Open Sans", Arial, sans-serif;
  }
  .canvas { position: relative; width: 1200px; height: 900px; }

  /* Front card */
  .card-front {
    position: absolute; left: 78px; top: 34px;
    width: 588px; height: 364px;
    background: var(--purple);
    box-shadow: 0 6px 18px rgba(0,0,0,0.15);
  }
  .card-front .brand-band {
    height: 156px; background: var(--white);
    display: flex; align-items: center; padding-left: 30px; gap: 28px;
  }
  .brand-mark {
    width: 74px; height: 74px; border-radius: 50%;
    background: var(--grey);
  }
  .brand-name {
    font-size: 50px; font-weight: 400; color: var(--grey); letter-spacing: 0.5px;
  }
  .holder { padding: 18px 0 0 30px; color: var(--white); }
  .holder-name { font-size: 20px; font-weight: 700; line-height: 1.2; }
  .holder-role { font-size: 15px; font-weight: 400; margin-top: 1px; }
  .contact-list {
    position: absolute; left: 0; top: 254px; width: 248px; list-style: none;
  }
  .contact-list li {
    height: 31.5px; display: flex; align-items: center; gap: 12px;
    padding-left: 32px; color: var(--white); font-size: 15px;
    border-bottom: 1px solid var(--rule);
  }
  .contact-list li:last-child { border-bottom: none; }
  .contact-list svg { width: 13px; height: 13px; fill: var(--white); flex: none; }
  .tagline {
    position: absolute; right: 30px; bottom: 24px;
    color: var(--white); font-size: 16px; font-weight: 600; letter-spacing: 0.4px;
  }

  /* Back card */
  .card-back {
    position: absolute; left: 388px; top: 505px;
    width: 567px; height: 352px;
    background: var(--purple);
    box-shadow: 0 6px 18px rgba(0,0,0,0.15);
  }
  .back-title {
    height: 84px; display: flex; align-items: center; justify-content: center;
    color: var(--white); font-size: 22px; font-weight: 600;
  }
  .booking-band {
    height: 170px; background: var(--white);
    padding: 24px 0 0 73px; color: var(--purple);
    font-size: 16px; font-weight: 600;
  }
  .field-row { display: flex; align-items: baseline; white-space: nowrap; line-height: 22px; }
  .field-row + .field-row { margin-top: 27px; }
  .fill-line {
    display: inline-block; border-bottom: 2px dotted var(--grey);
    height: 10px; margin: 0 6px;
  }
  .ampm { font-weight: 400; }
  .notice {
    height: 98px; display: flex; flex-direction: column; align-items: center;
    justify-content: center; color: var(--white); font-size: 19px; font-weight: 600;
    font-variant: small-caps; letter-spacing: 0.3px; line-height: 1.4; text-align: center;
  }
</style>
</head>
<body>
<main class="canvas">

  <section class="card-front" aria-label="Business card front">
    <header class="brand-band">
      <span class="brand-mark" aria-hidden="true"></span>
      <span class="brand-name">Gralo Tund</span>
    </header>
    <div class="holder">
      <p class="holder-name">Martin Holloway</p>
      <p class="holder-role">Managing Director</p>
    </div>
    <ul class="contact-list">
      <li>
        <svg viewBox="0 0 16 16" aria-hidden="true"><path d="M3.6 1.2l2.3 2.6c.3.4.3.9 0 1.3L4.8 6.3c.9 2 2.8 3.9 4.9 4.9l1.2-1.1c.4-.3.9-.3 1.3 0l2.6 2.3c.4.4.4 1 0 1.4l-1.3 1.3C11.2 16.4 0 5.2 1.1 2.9L2.3 1.2c.4-.4 1-.4 1.3 0z"/></svg>
        044-987 654 321
      </li>
      <li>
        <svg viewBox="0 0 16 16" aria-hidden="true"><path d="M1 3h14v10H1z M2 4.2v.4l6 4 6-4v-.4z" fill-rule="evenodd"/></svg>
        hello@gralotund.com
      </li>
      <li>
        <svg viewBox="0 0 16 16" aria-hidden="true"><path d="M6.5 9.5l3-3 1 1-3 3z M9 2.5a3 3 0 014.5 4.2l-1.6 1.6-1-1 1.6-1.6a1.6 1.6 0 00-2.3-2.3L8.6 5l-1-1z M7 14a3 3 0 01-4.5-4.2l1.6-1.6 1 1-1.6 1.6a1.6 1.6 0 002.3 2.3L7.4 11l1 1z"/></svg>
        www.gralotund.com
      </li>
    </ul>
    <p class="tagline">Relax, Renew, Revive</p>
  </section>

  <section class="card-back" aria-label="Appointment card back">
    <h2 class="back-title">Your Next Appointment on</h2>
    <div class="booking-band">
      <div class="field-row">Name :<span class="fill-line" style="width:352px"></span></div>
      <div class="field-row">Date :<span class="fill-line" style="width:120px"></span>&nbsp;&nbsp;Time :<span class="fill-line" style="width:110px"></span><span class="ampm">AM / PM</span></div>
      <div class="field-row">Date :<span class="fill-line" style="width:120px"></span>&nbsp;&nbsp;Time :<span class="fill-line" style="width:110px"></span><span class="ampm">AM / PM</span></div>
    </div>
    <footer class="notice">
      <span>If unable to keep appointment,</span>
      <span>kindly give 24hrs notice.</span>
    </footer>
  </section>

</main>
</body>
</html>
```